Brightmill Data Works

Our company is about IT hardwares and IT solutions. IT hardware such as PC, RAMS, storage and servers. IT solutions such as project management, BA. We are also selling new technology too.

Target Market(s)

Consumer, Small to Medium Business, Corporate

Requirements
Must have
• The business card must have the following:
• Name:
• Title:
• Contact Number:
• Email address:
• Website:
• Color: Must match the logo color upgrade

```html
<!DOCTYPE html>
<html lang="en">
<head>
<meta charset="utf-8">
<title>Brightmill Data Works – Business Card</title>
<link href="https://fonts.googleapis.com/css2?family=Rajdhani:wght@700&family=Lato:wght@400;700&display=swap" rel="stylesheet">
<style>
  :root {
    --backdrop: #2b2b2b;
    --card-white: #ffffff;
    --brand-orange: #c46a2c;
    --brand-orange-light: #d98a3a;
    --ink-dark: #3f3f3f;
    --ink-body: #1e1e1e;
    --rule: #333333;
  }
  * { margin: 0; padding: 0; box-sizing: border-box; }
  html, body { width: 1200px; height: 1200px; overflow: hidden; }
  body { background: var(--backdrop); position: relative; font-family: "Lato", sans-serif; }

  .card {
    position: absolute;
    top: 310px;
    width: 366px;
    height: 594px;
    box-shadow: 0 4px 14px rgba(0,0,0,0.45);
    text-align: center;
  }
  .card--front { left: 233px; background: var(--card-white); }
  .card--back { left: 627px; width: 369px; background: var(--brand-orange); }

  .brand-dot {
    position: absolute; left: 50%; top: 100px;
    width: 60px; height: 60px; margin-left: -30px;
    border-radius: 50%; background: var(--brand-orange-light);
  }
  .brand-name {
    position: absolute; left: 0; right: 0;
    font-family: "Rajdhani", sans-serif; font-weight: 700;
    font-size: 44px; line-height: 44px; letter-spacing: 1px;
    text-transform: uppercase;
  }
  .card--front .brand-name { top: 196px; color: var(--ink-dark); }
  .card--back .brand-name { top: 256px; color: var(--card-white); }

  .person { position: absolute; top: 366px; left: 0; right: 0; }
  .person__name { color: var(--brand-orange); font-size: 22px; font-weight: 400; letter-spacing: -0.3px; line-height: 26px; }
  .person__title { color: var(--ink-body); font-size: 17px; line-height: 22px; }

  .contact-divider {
    position: absolute; top: 448px; left: 88px;
    display: flex; align-items: center; gap: 3px;
  }
  .contact-divider__line { width: 52px; height: 1px; background: var(--rule); }
  .contact-divider svg { display: block; }

  .contact { position: absolute; top: 484px; left: 0; right: 0; color: var(--ink-body); font-size: 17px; line-height: 22px; }

  .tagline {
    position: absolute; top: 480px; left: 0; right: 0;
    color: var(--card-white); font-size: 21px; line-height: 38px; letter-spacing: -0.3px;
  }
</style>
</head>
<body>
  <section class="card card--front">
    <div class="brand-dot"></div>
    <div class="brand-name">Brightmill<br>Data Works</div>

    <div class="person">
      <p class="person__name">DANIEL OKAFOR</p>
      <p class="person__title">Managing Director</p>
    </div>

    <div class="contact-divider">
      <span class="contact-divider__line"></span>
      <svg width="24" height="24" viewBox="0 0 24 24" aria-label="Phone">
        <circle cx="12" cy="12" r="12" fill="#c46a2c"/>
        <path d="M6 10c0-2 3-3 6-3s6 1 6 3v1h-3v-1.5h-6V11H6z M8 12h8l1 5H7z" fill="#fff"/>
      </svg>
      <svg width="24" height="24" viewBox="0 0 24 24" aria-label="Email">
        <circle cx="12" cy="12" r="12" fill="#c46a2c"/>
        <rect x="6" y="8" width="12" height="8" fill="#fff"/>
        <path d="M6 8l6 5 6-5" fill="none" stroke="#c46a2c" stroke-width="1.2"/>
      </svg>
      <svg width="24" height="24" viewBox="0 0 24 24" aria-label="Website">
        <circle cx="12" cy="12" r="12" fill="#c46a2c"/>
        <circle cx="12" cy="12" r="6" fill="#fff"/>
        <path d="M9 9c2 0 2 2 4 2s1 3-1 3-1 2-2 2M14 8c1 1 2 1 3 3" fill="none" stroke="#c46a2c" stroke-width="1.3"/>
      </svg>
      <span class="contact-divider__line"></span>
    </div>

    <div class="contact">
      <p>044-987 650 312</p>
      <p>hello@brightmilldata.com</p>
      <p>www.brightmilldata.com</p>
    </div>
  </section>

  <section class="card card--back">
    <div class="brand-name">Brightmill<br>Data Works</div>
    <div class="tagline">IT HARDWARES<br>AND IT SOLUTIONS</div>
  </section>
</body>
</html>
```